Independent Financial Advisor Billboard Campaign - Maple Crest Financial

I am a local, independent financial advisor. My company is Maple Crest Financial, located in Charleston, WV. My main source of revenue comes from those nearing or entering retirement that need assistance with financial planning and investment management. Many are looking to rollover their employer retirement plan into an IRA account. I would like a billboard design campaign that focuses on this type of client. Please see our website www.maplecrestfinancial.com for more information.

```html
<!DOCTYPE html>
<html lang="en">
<head>
<meta charset="utf-8">
<title>Maple Crest Financial – Retirement Billboard</title>
<link rel="stylesheet" href="https://fonts.googleapis.com/css2?family=Cinzel:wght@700;900&family=Poppins:wght@600;700&display=swap">
<style>
  :root {
    --page-bg: #8e8e8e;
    --charcoal: #3a3a3a;
    --charcoal-deep: #2b2b2b;
    --brand-blue: #1f4a8f;
    --brand-blue-deep: #15397a;
    --white: #ffffff;
    --photo-warm: #d9c2a8;
    --photo-light: #eeeae4;
  }
  html, body {
    margin: 0;
    padding: 0;
    width: 1196px;
    height: 1200px;
    overflow: hidden;
    background: var(--page-bg);
  }
  .billboard {
    position: absolute;
    left: 48px;
    top: 440px;
    width: 1100px;
    height: 321px;
    box-shadow: 0 8px 18px rgba(0,0,0,0.35);
  }
  .billboard svg { display: block; width: 100%; height: 100%; }
  .headline {
    font-family: "Cinzel", "Times New Roman", serif;
    font-weight: 900;
    fill: var(--white);
  }
  .brand-name {
    font-family: "Cinzel", "Times New Roman", serif;
    font-weight: 700;
    fill: var(--white);
  }
  .phone {
    font-family: "Poppins", Arial, sans-serif;
    font-weight: 700;
    fill: var(--white);
  }
  .web {
    font-family: "Poppins", Arial, sans-serif;
    font-weight: 700;
    fill: var(--brand-blue-deep);
  }
</style>
</head>
<body>
  <div class="billboard">
    <svg viewBox="0 0 1320 385" xmlns="http://www.w3.org/2000/svg">
      <defs>
        <linearGradient id="bgCharcoal" x1="0" y1="0" x2="1" y2="1">
          <stop offset="0" stop-color="var(--charcoal-deep)"/>
          <stop offset="0.5" stop-color="var(--charcoal)"/>
          <stop offset="1" stop-color="var(--charcoal-deep)"/>
        </linearGradient>
        <linearGradient id="bandBlue" x1="0" y1="0" x2="1" y2="0">
          <stop offset="0" stop-color="var(--brand-blue-deep)"/>
          <stop offset="1" stop-color="var(--brand-blue)"/>
        </linearGradient>
        <linearGradient id="photoTone" x1="0" y1="0" x2="1" y2="1">
          <stop offset="0" stop-color="var(--photo-light)"/>
          <stop offset="0.55" stop-color="var(--photo-warm)"/>
          <stop offset="1" stop-color="var(--photo-light)"/>
        </linearGradient>
        <clipPath id="collageClip">
          <polygon points="1105,0 1320,0 1320,385 962,385 962,340 870,245"/>
        </clipPath>
      </defs>

      <rect class="backdrop" x="0" y="0" width="1320" height="385" fill="url(#bgCharcoal)"/>

      <rect class="contact-band" x="0" y="245" width="990" height="140" fill="url(#bandBlue)"/>

      <text class="headline" x="45" y="125" font-size="100" textLength="750" lengthAdjust="spacingAndGlyphs">RETIREMENT</text>
      <text class="headline" x="45" y="222" font-size="100" textLength="765" lengthAdjust="spacingAndGlyphs">DONE RIGHT!</text>

      <rect class="brand-mark" x="62" y="280" width="52" height="52" fill="var(--white)"/>
      <text class="brand-name" x="147" y="318" font-size="34" textLength="290" lengthAdjust="spacingAndGlyphs">Maple Crest</text>
      <text class="brand-name" x="197" y="347" font-size="17" textLength="193" lengthAdjust="spacing">FINANCIAL</text>

      <text class="phone" x="488" y="316" font-size="58" textLength="370" lengthAdjust="spacingAndGlyphs">304.555.0142</text>
      <rect class="web-box" x="480" y="328" width="482" height="32" fill="var(--white)"/>
      <text class="web" x="492" y="352" font-size="23" textLength="430" lengthAdjust="spacingAndGlyphs">www.maplecrestfinancial.com</text>

      <g class="photo-collage">
        <polygon points="1105,0 1320,0 1320,385 962,385 962,340 870,245" fill="url(#photoTone)"
                 role="img" aria-label="Photo collage: smiling advisor in a white polo shirt with retired couples enjoying time together"/>
        <g clip-path="url(#collageClip)" stroke="var(--brand-blue)" stroke-width="7" fill="none">
          <line x1="1190" y1="-20" x2="1330" y2="120"/>
          <line x1="1330" y1="80" x2="1210" y2="200"/>
          <line x1="1010" y1="120" x2="1120" y2="230"/>
          <line x1="1120" y1="230" x2="1040" y2="310"/>
        </g>
        <polyline points="1105,0 870,245 962,340" fill="none" stroke="var(--brand-blue)" stroke-width="8"/>
      </g>
    </svg>
  </div>
</body>
</html>
```